Webdesign für Steuerberaterin
Zielgruppe
Ich bin Steuerberaterin. Meine Zielgruppe sind sowohl Privatpersonen als auch Unternehmer sowie Männer und Frauen.
Aufgabenstellung
Bitte mein Logo und Foto mit berücksichtigen. Ich möchte keine Website, auf der alle 'Reiter' als eine Seite von oben nach unten durchlaufen. Sondern wirklich einzelne, voneinander getrennte Seiten.

```html
<!DOCTYPE html>
<html lang="de">
<head>
<meta charset="utf-8">
<title>Maren Brodtke – Steuerberaterin</title>
<link rel="stylesheet" href="https://fonts.googleapis.com/css2?family=EB+Garamond:wght@400&family=PT+Sans:wght@400;700&family=Cabin:wght@400&display=swap">
<style>
  :root {
    --sidebar: #1f252d;
    --gold: #c8963a;
    --gold-dark: #a8842a;
    --gold-line: #c9a43a;
    --footer: #d9b63a;
    --footer-text: #2b3038;
    --text: #4a4f55;
    --text-strong: #3d4146;
    --paper: #ffffff;
  }
  * { margin: 0; padding: 0; box-sizing: border-box; }
  html, body {
    width: 1200px; height: 768px; overflow: hidden;
    background: var(--paper);
  }
  .page { position: relative; width: 1200px; height: 768px; }

  .sidebar {
    position: absolute; left: 0; top: 0;
    width: 307px; height: 744px;
    background: var(--sidebar);
  }
  .main-nav { position: absolute; left: 80px; top: 0; }
  .main-nav a {
    position: absolute; left: 0; white-space: nowrap;
    font-family: "Cabin", sans-serif; font-size: 14px;
    color: var(--gold); text-decoration: none;
  }
  .main-nav .nav-about { top: 186px; }
  .main-nav .nav-services { top: 230px; left: 1px; }
  .main-nav .nav-contact { top: 277px; }

  .section-mark {
    position: absolute; left: 140px; top: 425px;
    width: 133px; height: 319px;
    border-radius: 66px 66px 40px 40px;
    background: linear-gradient(180deg, #e2dcd6 0%, #e2dcd6 40%, #34505f 60%, #2f4a58 100%);
    opacity: 0.9;
  }

  .brand {
    position: absolute; left: 370px; top: 110px;
    display: flex; align-items: center; gap: 8px;
  }
  .brand-dot {
    width: 12px; height: 12px; border-radius: 50%;
    background: var(--gold-dark);
  }
  .brand-name {
    font-family: "PT Sans", sans-serif; font-size: 20px; font-weight: 400;
    color: var(--gold-dark);
  }

  .portrait {
    position: absolute; left: 194px; top: 186px;
    width: 455px; height: 331px;
    background: radial-gradient(ellipse at 50% 45%, #f4f4f5 0%, #dcdcdf 55%, #c3c3c8 100%);
  }
  .portrait-figure {
    position: absolute; left: 125px; top: 30px;
    width: 215px; height: 301px;
    border-radius: 90px 90px 0 0;
    background: linear-gradient(180deg, #b89d8c 0%, #b89d8c 38%, #1c2233 46%, #1a1f2e 100%);
    opacity: 0.85;
  }

  .welcome {
    position: absolute; left: 691px; top: 0; width: 473px;
    text-align: center;
  }
  .welcome-title {
    position: absolute; left: 0; top: 137px; width: 100%;
    font-family: "EB Garamond", serif; font-weight: 400; font-size: 24px;
    color: var(--gold-dark);
  }
  .welcome-rule {
    position: absolute; left: 0; top: 187px; width: 473px;
    height: 2px; background: var(--gold-line); border: 0;
  }
  .welcome-lead {
    position: absolute; left: -20px; top: 224px; width: 513px;
    font-family: "PT Sans", sans-serif; font-weight: 700; font-size: 14.5px;
    color: var(--text-strong);
  }
  .welcome-text {
    position: absolute; left: -40px; width: 553px;
    font-family: "PT Sans", sans-serif; font-size: 14px; line-height: 17.8px;
    color: var(--text);
  }
  .welcome-text.p1 { top: 263px; }
  .welcome-text.p2 { top: 373px; }
  .welcome-text.p3 { top: 447px; }

  .site-footer {
    position: absolute; left: 0; top: 744px;
    width: 1200px; height: 24px;
    background: var(--footer);
  }
  .legal-links {
    position: absolute; left: 80px; top: 3px;
    font-family: "Cabin", sans-serif; font-size: 13.5px;
    color: var(--footer-text); white-space: nowrap;
  }
  .legal-links a { color: inherit; text-decoration: none; }
  .legal-links .divider { margin: 0 8px; }
</style>
</head>
<body>
<div class="page">
  <aside class="sidebar">
    <nav class="main-nav">
      <a class="nav-about" href="#">Über mich</a>
      <a class="nav-services" href="#">Leistungen</a>
      <a class="nav-contact" href="#">Kontakt</a>
    </nav>
  </aside>

  <div class="section-mark" role="img" aria-label="Großes dekoratives Paragraphenzeichen in Beige und Petrol"></div>

  <div class="brand">
    <span class="brand-dot"></span>
    <span class="brand-name">Maren Brodtke</span>
  </div>

  <div class="portrait" role="img" aria-label="Porträtfoto der Steuerberaterin vor heller Steinwand">
    <div class="portrait-figure"></div>
  </div>

  <section class="welcome">
    <h1 class="welcome-title">Schön, dass Sie da sind</h1>
    <hr class="welcome-rule">
    <p class="welcome-lead">Ich freue mich, dass Sie den Weg zu mir gefunden haben!</p>
    <p class="welcome-text p1">Sie sind bei mir genau richtig:<br>
      Egal, ob Sie Privatperson sind, die Ihre Einkommensteuer-Erklärung<br>
      in vertrauensvolle Hände geben möchte,<br>
      oder Unternehmer, der sich z.B. das „Rundum-Sorglos-Paket“<br>
      mit Buchführung, Jahresabschluss und Steuererklärungen wünscht.</p>
    <p class="welcome-text p2">Schauen Sie sich hier gerne um und melden Sie sich bei mir<br>
      – ich bin bei jedem steuerlichen Thema<br>
      gerne Ihr kompetenter und zuverlässiger Ansprechpartner.</p>
    <p class="welcome-text p3">Für mich ist es eine Selbstverständlichkeit,<br>
      dass ich auch nach mehr als 12 Jahren Berufserfahrung<br>
      durch permanente Fortbildungen immer auf dem aktuellsten Stand<br>
      der relevanten Gesetze und Verordnungen bin.<br>
      Nur so kann ich Sie bestmöglich beraten.</p>
  </section>

  <footer class="site-footer">
    <div class="legal-links">
      <a href="#">Impressum</a><span class="divider">|</span><a href="#">Datenschutz</a>
    </div>
  </footer>
</div>
</body>
</html>
```